creative pack design with extended budget for Zulimbo coffee product

- we need a packing design for a new product of coffee for our company Mireko Dasu located in Uganda.
- specialty Arabica coffee grown at slopes of Mountain Elgon with rich volcanic soils located in Eastern region of Uganda.
-  we have a logo already made and has registered in Uganda. our logo colors are mixture between a lot of brown color and yellow. vacuum  plastic bags.
- there is no restrictions towards your imagination .
-  all details available
- we will launch our product through phases ;
- phase 1 is  a ground coffee : ( Turkish coffee )  2 degrees of roasting which are ( medium dark , light ) of 250 grm
b) roasted beans: 2 degrees ( medium, dark) of 250 grm & 1000 grm
- we need also to highlight the eastern spirit of Turkish coffee
- we  need designs, the info and color only will be changed depending on previous classifications

Target Market(s)
Arab countries, Turkey , Uganda, Europe
Colors
Designer to choose colors to be used in the design.
Requirements
Nice to have
- about nature , Elgon mountain , farmers, freshness, distinctive product, soul of east such as decorated cup of Turkish coffee . these just an ideas but there is no restrictions on your imagination

```html
<!DOCTYPE html>
<html lang="en">
<head>
<meta charset="utf-8">
<title>Zulimbo Arabica Coffee – Pack Front</title>
<link rel="stylesheet" href="https://fonts.googleapis.com/css2?family=Great+Vibes&family=Montserrat:wght@500;700&family=Lato:wght@400&display=swap">
<style>
  :root {
    --backdrop: #c4c4c4;
    --pack-blue: #4dbbd8;
    --pack-blue-deep: #3aa8c6;
    --crimp-line: #3a9fbb;
    --brand-brown: #5a2a1c;
    --script-white: #f4f7f8;
    --accent-yellow: #e4c430;
    --band-text: #fdf7dc;
    --art-ink: #2a6679;
    --art-mid: #3f90a8;
    --art-light: #7fcfe3;
  }
  html, body {
    margin: 0;
    padding: 0;
    width: 1200px;
    height: 1200px;
    overflow: hidden;
    background: var(--backdrop);
  }
  .canvas {
    position: relative;
    width: 1200px;
    height: 1200px;
  }
  .pack-front {
    position: absolute;
    left: 330px;
    top: 30px;
    width: 540px;
    height: 1140px;
    background: linear-gradient(180deg, var(--pack-blue) 0%, var(--pack-blue) 85%, var(--pack-blue-deep) 100%);
  }
  .pack-crimp {
    position: absolute;
    left: 0;
    top: 0;
    width: 540px;
    height: 42px;
  }
  .brand-mark {
    position: absolute;
    top: 190px;
    left: 0;
    width: 100%;
    display: flex;
    align-items: center;
    justify-content: center;
    gap: 14px;
  }
  .brand-dot {
    width: 30px;
    height: 30px;
    border-radius: 50%;
    background: var(--brand-brown);
  }
  .brand-name {
    font-family: "Montserrat", sans-serif;
    font-weight: 700;
    font-size: 46px;
    letter-spacing: 2px;
    color: var(--brand-brown);
    text-transform: uppercase;
  }
  .variety-title {
    position: absolute;
    top: 345px;
    left: 0;
    width: 100%;
    text-align: center;
    font-family: "Great Vibes", cursive;
    font-size: 108px;
    line-height: 1;
    color: var(--script-white);
  }
  .variety-sub {
    position: absolute;
    top: 452px;
    left: 0;
    width: 100%;
    padding-left: 90px;
    box-sizing: border-box;
    text-align: center;
    font-family: "Montserrat", sans-serif;
    font-weight: 500;
    font-size: 42px;
    letter-spacing: 3px;
    line-height: 1;
    color: var(--accent-yellow);
  }
  .farmer-artwork {
    position: absolute;
    left: 75px;
    top: 510px;
    width: 420px;
    height: 440px;
  }
  .info-band {
    position: absolute;
    left: 76px;
    top: 964px;
    width: 414px;
    height: 66px;
    background: var(--accent-yellow);
    display: flex;
    align-items: center;
    justify-content: space-between;
    padding: 0 24px 0 14px;
    box-sizing: border-box;
    font-family: "Lato", sans-serif;
    font-size: 25px;
    color: var(--band-text);
  }
  .info-weight {
    letter-spacing: 1px;
  }
</style>
</head>
<body>
<div class="canvas">
  <div class="pack-front">
    <svg class="pack-crimp" viewBox="0 0 540 42" aria-hidden="true">
      <g stroke="var(--crimp-line)" stroke-width="2">
        <line x1="0" y1="8" x2="540" y2="8"/>
        <line x1="0" y1="16" x2="540" y2="16"/>
        <line x1="0" y1="24" x2="540" y2="24"/>
        <line x1="0" y1="32" x2="540" y2="32"/>
        <line x1="0" y1="40" x2="540" y2="40"/>
      </g>
    </svg>

    <div class="brand-mark">
      <span class="brand-dot"></span>
      <span class="brand-name">Zulimbo</span>
    </div>

    <div class="variety-title">Arabica</div>
    <div class="variety-sub">COFFEE</div>

    <svg class="farmer-artwork" viewBox="0 0 420 440" role="img" aria-label="Line illustration of a woman farmer sorting coffee cherries in a basket, framed by coffee branches with Mount Elgon slopes behind">
      <defs>
        <linearGradient id="artwork-tone" x1="0" y1="0" x2="0" y2="1">
          <stop offset="0%" stop-color="var(--art-light)"/>
          <stop offset="35%" stop-color="var(--art-mid)"/>
          <stop offset="100%" stop-color="var(--art-ink)"/>
        </linearGradient>
      </defs>
      <rect x="0" y="0" width="420" height="440" rx="24" fill="url(#artwork-tone)" opacity="0.55"/>
    </svg>

    <div class="info-band">
      <span class="info-grind">ground coffee</span>
      <span class="info-weight">250 grama</span>
    </div>
  </div>
</div>
</body>
</html>
```